DJ Colm Vetter

I'm looking for a professional but still artsy/progressive design. I come from a hip hop/club DJ background playing a lot of underground music but have switched to doing more corporate parties and weddings recently. I am all about keeping the dancefloor moving and emotionally connecting with the crowd. I'd like a trendy/updated color palette. Something that's clean enough that looks professional but also trendy enough to convey that by the end of the night we'll be sweatily dancing to the latest hits. Some designers/artists I like: Tarn Olquist, Pavel Remy, Wendell Quarrie, Lumeno 7400, Silas Dravin.

```html
<!DOCTYPE html>
<html lang="en">
<head>
<meta charset="utf-8">
<title>DJ Colm Vetter – Business Card</title>
<link rel="stylesheet" href="https://fonts.googleapis.com/css2?family=Bebas+Neue&family=Open+Sans:wght@400;600&display=swap">
<style>
  :root {
    --backdrop: #7b7b7b;
    --card-light: #eeeeee;
    --card-dark: #252424;
    --ink: #111111;
    --ink-soft: #1f1f1f;
    --accent: #ee7a1c;
    --white: #ffffff;
    --rule: #9a9a9a;
  }
  * { margin: 0; padding: 0; box-sizing: border-box; }
  html, body {
    width: 1200px; height: 1200px; overflow: hidden;
    background: var(--backdrop);
  }
  .canvas { position: relative; width: 1200px; height: 1200px; }

  .card {
    position: absolute; top: 310px; width: 366px; height: 594px;
    box-shadow: 2px 3px 6px rgba(0,0,0,.35);
    text-align: center;
  }
  .card--front { left: 234px; background: var(--card-light); }
  .card--back  { left: 629px; background: var(--card-dark); }

  .wordmark {
    position: absolute; left: 0; right: 0;
    font-family: "Bebas Neue", "Oswald", sans-serif;
    font-size: 56px; line-height: 1; letter-spacing: .5px;
  }
  .card--front .wordmark { top: 170px; color: var(--ink); }
  .card--back  .wordmark { top: 272px; color: var(--white); }

  .contact { position: absolute; left: 0; right: 0; top: 340px; font-family: "Open Sans", sans-serif; color: var(--ink-soft); }
  .contact__name {
    font-family: "Bebas Neue", "Oswald", sans-serif;
    font-size: 30px; line-height: 1; color: var(--accent); letter-spacing: .3px;
  }
  .contact__role { font-size: 17px; line-height: 22px; margin-top: 2px; }
  .contact__rule { width: 207px; height: 1px; background: var(--rule); margin: 8px auto 9px; }
  .contact__line { font-size: 17px; line-height: 21.5px; }
  .contact__label { color: var(--accent); }
  .contact__web { color: var(--accent); }
  .contact__address { font-size: 17px; line-height: 21.5px; }

  .back__web {
    position: absolute; left: 0; right: 0; top: 510px;
    font-family: "Open Sans", sans-serif; font-weight: 600;
    font-size: 19px; color: var(--accent);
  }
</style>
</head>
<body>
<main class="canvas">
  <section class="card card--front">
    <h1 class="wordmark">DJ Colm Vetter</h1>
    <div class="contact">
      <p class="contact__name">Aldo Brenner</p>
      <p class="contact__role">Managing Director</p>
      <div class="contact__rule"></div>
      <p class="contact__line"><span class="contact__label">P:</span> 055-987 210 346</p>
      <p class="contact__line"><span class="contact__label">M:</span> 055-987 210 346</p>
      <p class="contact__line"><span class="contact__label">E:</span> hello@vettersound.com</p>
      <p class="contact__line contact__web">www.vettersound.com</p>
      <div class="contact__rule"></div>
      <p class="contact__address">4821, Harbor Line Road</p>
      <p class="contact__address">Northland, 604218.</p>
    </div>
  </section>

  <section class="card card--back">
    <p class="wordmark">DJ Colm Vetter</p>
    <p class="back__web">www.vettersound.com</p>
  </section>
</main>
</body>
</html>
```